1 Banner für Affiliate-Marketing (Börse/Trading)
Zielgruppe
Wir vermitteln Kunden an einen Broker. Die Kunden eröffnen Handelskonten, in denen sie selbständig Finanzprodukte (CFDs, Forex, Aktien, Edelmetalle,...) gehebelt handeln. Wir bieten dem Kunden eine Dienstleistung an, indem wir Broker vorauswählen, technischen Support liefern, bei der Kontoeröffnung unterstützen und auf Wunsch auch Trader ausbilden.
Zielgruppe: männlich, finanz- und risikoaffin, Spekulant
Aufgabenstellung
Wir benötigen 1 klickstarken Banner für das Affiliate-Marketing
Bannergröße: 300*250
Formate: GIF, PNG, JPG, Vektor
Gerne auch animierte Vorschläge, aber bitte nicht ausschließlich.
Zusätzliche Info, die verarbeitet werden kann (aber nicht muss): Kelvora Bank hat in 2016 bei 2 Kundenumfragen den Testsieg als bester Broker gewonnen.
Design ist frei und muss sich nicht an der Homepage orientieren - vielmehr suchen wir klickstarke Banner aus der Finanz-/Börsenwelt mit Bildern Ihrer Wahl.

```html
<!DOCTYPE html>
<html lang="de">
<head>
<meta charset="utf-8">
<title>Kelvora Bank – Bannerset Bester Broker</title>
<link rel="stylesheet" href="https://fonts.googleapis.com/css2?family=Ubuntu:wght@500;700&display=swap">
<style>
  :root{
    --stage:#232323;
    --label:#e8e8e8;
    --yellow:#ffd400;
    --yellow-deep:#e9b800;
    --navy:#0b1f5c;
    --blue-1:#2a63c9;
    --blue-2:#1546a6;
    --blue-3:#0a2d78;
    --blue-4:#061c4e;
    --white:#ffffff;
    --device:#0c0f1a;
  }
  *{box-sizing:border-box;margin:0;padding:0}
  html,body{width:1200px;height:857px;overflow:hidden;background:var(--stage)}
  body{position:relative;font-family:"Ubuntu",sans-serif}

  .size-label{position:absolute;color:var(--label);font-size:15px;font-weight:700;letter-spacing:.5px;font-family:"Ubuntu",sans-serif}

  .banner{position:absolute;overflow:hidden;background:var(--blue-2)}
  .banner__scene{position:absolute;inset:0;
    background:
      radial-gradient(ellipse at 75% 60%, rgba(5,20,60,.55), transparent 55%),
      linear-gradient(160deg,var(--blue-1) 0%,var(--blue-2) 45%,var(--blue-3) 80%,var(--blue-4) 100%);}
  .banner__device{position:absolute;background:linear-gradient(150deg,#1b2a55 0%,#14336f 40%,var(--device) 100%);border-radius:6px;border:3px solid var(--device)}

  .brand{position:absolute;left:0;top:0;background:var(--yellow);color:var(--navy);font-weight:700;line-height:.95;display:flex;flex-direction:column;justify-content:center;text-transform:uppercase}
  .brand--slant{clip-path:polygon(0 0,100% 0,86% 100%,0 100%);padding-left:7px}
  .brand--header{width:100%;align-items:center;text-align:center;clip-path:polygon(0 0,100% 0,100% 88%,50% 100%,0 88%)}

  .copy{position:absolute;text-align:center;text-transform:uppercase;font-weight:700}
  .line{position:absolute;left:0;right:0;line-height:1;white-space:nowrap;text-align:center}
  .line--white{color:var(--white)}
  .line--yellow{color:var(--yellow)}
  .best{color:var(--white)}
  .broker{position:absolute;background:var(--yellow);color:var(--navy);display:flex;align-items:center;justify-content:center;font-weight:700;line-height:1}
  .won{color:var(--white)}

  .cta{position:absolute;border-radius:5px;background:linear-gradient(180deg,#ffe34a 0%,var(--yellow) 45%,var(--yellow-deep) 100%);color:var(--navy);font-weight:700;display:flex;align-items:center;justify-content:space-between;text-transform:uppercase;box-shadow:0 1px 3px rgba(0,0,0,.45);white-space:nowrap}
  .cta svg{display:block;flex:none}
</style>
</head>
<body>

<!-- 728 x 90 -->
<div class="size-label" style="left:58px;top:89px">728 X 90</div>
<div class="banner" style="left:57px;top:122px;width:624px;height:77px">
  <div class="banner__scene" role="img" aria-label="Blauer Börsenhintergrund mit Kurslinien und Silhouette eines Geschäftsmanns"></div>
  <div class="banner__device" role="img" aria-label="Tablet mit Börsenchart" style="left:548px;top:-6px;width:90px;height:48px"></div>
  <div class="brand brand--slant" style="width:136px;height:77px;font-size:22px">KELVORA<br>BANK</div>
  <div class="copy" style="left:138px;width:186px;top:0;height:77px">
    <div class="line line--white" style="top:11px;font-size:14px">HAT IN <span class="line--yellow" style="font-size:16px">2016 BEI 2</span></div>
    <div class="line line--yellow" style="top:31px;font-size:15.5px">KUNDENUMFRAGEN</div>
    <div class="line line--white" style="top:52px;font-size:12.5px">DEN TESTSIEG ALS</div>
  </div>
  <div class="copy" style="left:334px;width:97px;top:0;height:77px">
    <div class="line best" style="top:6px;font-size:26px">BESTER</div>
    <div class="broker" style="left:0;top:33px;width:97px;height:16px;font-size:12px;letter-spacing:5px;padding-left:5px">BROKER</div>
    <div class="line won" style="top:53px;font-size:15px">GEWONNEN</div>
  </div>
  <div class="cta" style="left:500px;top:45px;width:114px;height:23px;font-size:11px;padding:0 3px 0 8px">HIER KLICKEN
    <svg width="18" height="18" viewBox="0 0 18 18" aria-hidden="true"><circle cx="9" cy="9" r="9" fill="#c99a00"/><path d="M7 4.5 L11.5 9 L7 13.5" fill="none" stroke="#fff3a0" stroke-width="2.4" stroke-linecap="round"/></svg>
  </div>
</div>

<!-- 468 x 60 -->
<div class="size-label" style="left:704px;top:89px">468 X 60</div>
<div class="banner" style="left:702px;top:122px;width:401px;height:51px">
  <div class="banner__scene" role="img" aria-label="Blauer Börsenhintergrund mit Kurslinien"></div>
  <div class="brand brand--slant" style="width:85px;height:51px;font-size:14px;padding-left:5px">KELVORA<br>BANK</div>
  <div class="copy" style="left:88px;width:122px;top:0;height:51px">
    <div class="line line--white" style="top:6px;font-size:10px">HAT IN <span class="line--yellow" style="font-size:11px">2016 BEI 2</span></div>
    <div class="line line--yellow" style="top:19px;font-size:11.5px">KUNDENUMFRAGEN</div>
    <div class="line line--white" style="top:34px;font-size:9.5px">DEN TESTSIEG ALS</div>
  </div>
  <div class="copy" style="left:221px;width:67px;top:0;height:51px">
    <div class="line best" style="top:2px;font-size:18px">BESTER</div>
    <div class="broker" style="left:0;top:21px;width:67px;height:11px;font-size:9px;letter-spacing:3px;padding-left:3px">BROKER</div>
    <div class="line won" style="top:35px;font-size:10px">GEWONNEN</div>
  </div>
  <div class="cta" style="left:306px;top:14px;width:87px;height:22px;font-size:11px;justify-content:center">HIER KLICKEN</div>
</div>

<!-- 120 x 600 -->
<div class="size-label" style="left:57px;top:768px">120 X 600</div>
<div class="banner" style="left:57px;top:243px;width:103px;height:514px">
  <div class="banner__scene" role="img" aria-label="Blauer Börsenhintergrund mit Silhouette eines Geschäftsmanns"></div>
  <div class="banner__device" role="img" aria-label="Tablet mit Börsenchart" style="left:-6px;top:387px;width:100px;height:140px"></div>
  <div class="brand brand--header" style="height:66px;font-size:18px">KELVORA<br>BANK</div>
  <div class="copy" style="left:0;width:103px;top:0;height:260px">
    <div class="line line--white" style="top:101px;font-size:15px">HAT IN</div>
    <div class="line line--yellow" style="top:118px;font-size:15px">2016 BEI 2</div>
    <div class="line line--yellow" style="top:135px;font-size:9.5px">KUNDENUMFRAGEN</div>
    <div class="line line--white" style="top:147px;font-size:9.5px">DEN TESTSIEG ALS</div>
    <div class="line best" style="top:166px;font-size:25px">BESTER</div>
    <div class="broker" style="left:5px;top:192px;width:93px;height:17px;font-size:12px;letter-spacing:5px;padding-left:5px">BROKER</div>
    <div class="line won" style="top:211px;font-size:15px">GEWONNEN</div>
  </div>
  <div class="cta" style="left:3px;top:486px;width:97px;height:19px;font-size:9.5px;padding:0 2px 0 6px">HIER KLICKEN
    <svg width="15" height="15" viewBox="0 0 18 18" aria-hidden="true"><circle cx="9" cy="9" r="9" fill="#c99a00"/><path d="M7 4.5 L11.5 9 L7 13.5" fill="none" stroke="#fff3a0" stroke-width="2.4" stroke-linecap="round"/></svg>
  </div>
</div>

<!-- 160 x 600 -->
<div class="size-label" style="left:203px;top:768px">160 X 600</div>
<div class="banner" style="left:200px;top:243px;width:137px;height:514px">
  <div class="banner__scene" role="img" aria-label="Blauer Börsenhintergrund mit Silhouette eines Geschäftsmanns"></div>
  <div class="banner__device" role="img" aria-label="Tablet mit Börsenchart" style="left:-6px;top:388px;width:128px;height:140px"></div>
  <div class="brand brand--header" style="height:62px;font-size:25px">KELVORA<br>BANK</div>
  <div class="copy" style="left:0;width:137px;top:0;height:260px">
    <div class="line line--white" style="top:97px;font-size:14px">HAT IN</div>
    <div class="line line--yellow" style="top:116px;font-size:17px">2016 BEI 2</div>
    <div class="line line--yellow" style="top:134px;font-size:12px">KUNDENUMFRAGEN</div>
    <div class="line line--white" style="top:149px;font-size:11px">DEN TESTSIEG ALS</div>
    <div class="line best" style="top:172px;font-size:34px">BESTER</div>
    <div class="broker" style="left:7px;top:207px;width:123px;height:22px;font-size:17px;letter-spacing:7px;padding-left:7px">BROKER</div>
    <div class="line won" style="top:232px;font-size:20px">GEWONNEN</div>
  </div>
  <div class="cta" style="left:4px;top:477px;width:128px;height:26px;font-size:13px;padding:0 3px 0 10px">HIER KLICKEN
    <svg width="19" height="19" viewBox="0 0 18 18" aria-hidden="true"><circle cx="9" cy="9" r="9" fill="#c99a00"/><path d="M7 4.5 L11.5 9 L7 13.5" fill="none" stroke="#fff3a0" stroke-width="2.4" stroke-linecap="round"/></svg>
  </div>
</div>

<!-- 500 x 500 -->
<div class="size-label" style="left:379px;top:693px">500 X 500</div>
<div class="banner" style="left:377px;top:243px;width:429px;height:429px">
  <div class="banner__scene" role="img" aria-label="Blauer Börsenhintergrund mit Kurszahlen und Silhouette eines Geschäftsmanns"></div>
  <div class="banner__device" role="img" aria-label="Tablet mit Börsenchart" style="left:-8px;top:296px;width:162px;height:145px"></div>
  <div class="brand brand--header" style="height:58px;font-size:42px;padding-bottom:6px">KELVORA BANK</div>
  <div class="copy" style="left:62px;width:310px;top:0;height:300px">
    <div class="line line--white" style="top:84px;font-size:16px">HAT IN</div>
    <div class="line line--yellow" style="top:104px;font-size:19px">2016 BEI 2 KUNDENUMFRAGEN</div>
    <div class="line line--white" style="top:125px;font-size:16px">DEN TESTSIEG ALS</div>
    <div class="line best" style="top:155px;font-size:57px">BESTER</div>
    <div class="broker" style="left:51px;top:211px;width:208px;height:42px;font-size:31px;letter-spacing:13px;padding-left:13px">BROKER</div>
    <div class="line won" style="top:256px;font-size:34px">GEWONNEN</div>
  </div>
  <div class="cta" style="left:190px;top:363px;width:224px;height:47px;font-size:23px;padding:0 4px 0 16px;border-radius:8px">HIER KLICKEN
    <svg width="38" height="38" viewBox="0 0 18 18" aria-hidden="true"><circle cx="9" cy="9" r="9" fill="#c99a00"/><path d="M7 4.5 L11.5 9 L7 13.5" fill="none" stroke="#fff3a0" stroke-width="2" stroke-linecap="round"/></svg>
  </div>
</div>

<!-- 300 x 250 -->
<div class="size-label" style="left:845px;top:473px">300 X 250</div>
<div class="banner" style="left:846px;top:243px;width:257px;height:214px">
  <div class="banner__scene" role="img" aria-label="Blauer Börsenhintergrund mit Kurslinien und Silhouette eines Geschäftsmanns"></div>
  <div class="banner__device" role="img" aria-label="Tablet mit Börsenchart" style="left:-6px;top:155px;width:82px;height:66px"></div>
  <div class="brand brand--header" style="height:44px;font-size:27px;padding-bottom:4px">KELVORA BANK</div>
  <div class="copy" style="left:56px;width:150px;top:0;height:175px">
    <div class="line line--white" style="top:49px;font-size:11px">HAT IN</div>
    <div class="line line--yellow" style="top:64px;font-size:13px">2016 BEI 2</div>
    <div class="line line--yellow" style="top:79px;font-size:13px">KUNDENUMFRAGEN</div>
    <div class="line line--white" style="top:94px;font-size:10px">DEN TESTSIEG ALS</div>
    <div class="line best" style="top:114px;font-size:25px">BESTER</div>
    <div class="broker" style="left:30px;top:139px;width:92px;height:17px;font-size:12px;letter-spacing:5px;padding-left:5px">BROKER</div>
    <div class="line won" style="top:157px;font-size:15px">GEWONNEN</div>
  </div>
  <div class="cta" style="left:132px;top:183px;width:117px;height:23px;font-size:12px;padding:0 3px 0 8px">HIER KLICKEN
    <svg width="18" height="18" viewBox="0 0 18 18" aria-hidden="true"><circle cx="9" cy="9" r="9" fill="#c99a00"/><path d="M7 4.5 L11.5 9 L7 13.5" fill="none" stroke="#fff3a0" stroke-width="2.4" stroke-linecap="round"/></svg>
  </div>
</div>

</body>
</html>
```